Website Quibrel Outdoor

Hi I'm looking for a simple design for a new website. It's outdoor products mainly in category, Boat, Tarpaulin, Fishing, Golf. I have include image and text for 8 products + presentation etc. I want a simple and modern site + fast + Mobile. Wordpress. I'm going to sell through Tradovik so I don't need any WooCommerce but a buy button to Tradovik. I haven set up the Tradovik account yet. My logo i s grey and orange. My goal is to sell in Tradovik US and later EU.

```html
<!DOCTYPE html>
<html lang="en">
<head>
<meta charset="utf-8">
<title>Quibrel Outdoor</title>
<link href="https://fonts.googleapis.com/css2?family=Montserrat:wght@500;600;700;800&family=Open+Sans:wght@400;600&display=swap" rel="stylesheet">
<style>
:root{
  --orange:#f08a24;
  --orange-dark:#e0731a;
  --ink:#222;
  --grey:#6b6b6b;
  --light:#f2f2f2;
  --footer:#262626;
  --white:#fff;
}
*{box-sizing:border-box;margin:0;padding:0}
html,body{width:1200px;height:3528px;overflow:hidden}
body{font-family:"Open Sans",Arial,sans-serif;color:var(--ink);background:var(--white);position:relative}
.heading{font-family:"Montserrat",Arial,sans-serif;font-weight:700;text-align:center;font-size:40px;letter-spacing:1px;color:var(--ink)}
.heading::after{content:"";display:block;width:64px;height:4px;background:var(--orange);margin:14px auto 0}
.btn{display:inline-block;font-family:"Montserrat",Arial,sans-serif;font-weight:700;font-size:14px;padding:12px 22px;background:var(--orange);color:var(--white);text-transform:uppercase;border-radius:3px}
.btn-outline{background:var(--white);color:var(--ink);border:2px solid var(--ink)}

/* header */
.site-header{position:absolute;top:0;left:0;width:1200px;height:64px;background:var(--white);z-index:3;display:flex;align-items:center;font-family:"Montserrat",Arial,sans-serif;font-weight:600;font-size:16px}
.nav-left{position:absolute;left:190px;display:flex;gap:44px}
.nav-right{position:absolute;left:720px;display:flex;gap:44px;align-items:center}
.brand-badge{position:absolute;left:510px;top:0;width:180px;height:140px;background:var(--white);border-radius:0 0 90px 90px;display:flex;flex-direction:column;align-items:center;justify-content:center;z-index:4}
.brand-badge .dot{width:26px;height:26px;border-radius:50%;background:var(--grey);margin-bottom:8px}
.brand-badge .name{font-family:"Montserrat",Arial,sans-serif;font-weight:800;font-size:22px;color:var(--orange);letter-spacing:1px}
.brand-badge .sub{font-family:"Montserrat",Arial,sans-serif;font-weight:800;font-size:12px;color:var(--orange);letter-spacing:3px}

/* hero */
.hero{position:absolute;top:0;left:0;width:1200px;height:740px}
.hero-photo{position:absolute;inset:0;background:linear-gradient(100deg,#d9a27e 0%,#8e7f86 45%,#4d4f5c 100%)}
.hero-curve{position:absolute;left:0;bottom:0}
.hero-copy{position:absolute;left:160px;top:290px;color:var(--white);width:460px}
.hero-copy h1{font-family:"Montserrat",Arial,sans-serif;font-weight:800;font-size:52px;letter-spacing:1px}
.hero-copy p{font-size:16px;line-height:24px;margin:12px 0 28px}
.slide-arrow{position:absolute;top:380px;width:40px;height:40px;border-radius:50%;background:var(--white);display:flex;align-items:center;justify-content:center}

/* products */
.products{position:absolute;left:0;width:1200px}
.products .heading{margin-bottom:48px}
.product-row{display:flex;justify-content:center;gap:40px}
.product-card{width:200px;height:272px;background:var(--white);box-shadow:0 2px 10px rgba(0,0,0,.12);display:flex;flex-direction:column;align-items:center;padding:18px 10px}
.product-card .thumb{width:120px;height:110px;border-radius:4px}
.product-card h3{font-size:12px;font-weight:600;margin-top:18px;text-transform:uppercase}
.product-card .price{color:var(--orange);font-weight:600;font-size:18px;margin:8px 0 10px}
.product-card .btn{font-size:11px;padding:7px 12px;font-family:"Open Sans",Arial,sans-serif;font-weight:600;text-transform:none}

/* about */
.about{position:absolute;top:1266px;left:0;width:1200px;height:380px;background:var(--light)}
.about-photo{position:absolute;left:0;top:0;width:600px;height:380px;background:linear-gradient(135deg,#e8e4dc,#9a8a6c)}
.about-card{position:absolute;left:600px;top:64px;width:480px;height:380px;background:var(--white);box-shadow:0 4px 18px rgba(0,0,0,.15);padding:40px 40px}
.about-card h2{font-family:"Montserrat",Arial,sans-serif;font-weight:700;font-size:36px}
.about-card h2::after{content:"";display:block;width:56px;height:4px;background:var(--orange);margin-top:10px}
.about-card p{font-size:14px;line-height:24px;color:var(--grey);margin:22px 0 26px}

/* newsletter */
.newsletter{position:absolute;top:2248px;left:0;width:1200px;height:296px;background:linear-gradient(120deg,var(--orange-dark),var(--orange));text-align:center;color:var(--white);padding-top:70px}
.newsletter h2{font-family:"Montserrat",Arial,sans-serif;font-weight:700;font-size:40px}
.newsletter p{width:700px;margin:12px auto 26px;font-size:14px;line-height:22px}
.signup{display:flex;justify-content:center}
.signup .field{width:350px;height:50px;background:var(--white);color:#888;text-align:left;padding:14px 18px;font-size:15px}
.signup .submit{width:150px;height:50px;border:1px solid var(--white);color:var(--white);padding-top:14px;font-size:15px;margin-left:10px}

/* blog */
.blog{position:absolute;top:2612px;left:0;width:1200px}
.blog .heading{margin-bottom:48px}
.blog-row{display:flex;justify-content:center;gap:24px}
.post{width:308px;background:var(--white);box-shadow:0 2px 12px rgba(0,0,0,.12)}
.post .photo{height:170px}
.post .body{padding:16px 26px 20px}
.post .date{display:inline-block;background:var(--orange);color:var(--white);font-size:12px;padding:3px 10px;margin-top:-30px;position:relative}
.post h3{font-family:"Montserrat",Arial,sans-serif;font-weight:700;font-size:15px;margin:8px 0 6px}
.post p{font-size:13px;line-height:19px;color:var(--grey)}
.post .more{color:var(--orange);font-size:14px;margin-top:10px}

/* footer */
.site-footer{position:absolute;top:3100px;left:0;width:1200px;height:428px;background:var(--footer);color:var(--white)}
.footer-curve{position:absolute;top:0;left:0}
.footer-col{position:absolute;top:150px}
.footer-col h4{font-family:"Montserrat",Arial,sans-serif;font-weight:700;font-size:16px;margin-bottom:16px}
.footer-col li{list-style:none;font-size:15px;line-height:30px}
.footer-col li::before{content:"›";color:var(--orange);margin-right:8px}
.footer-brand{position:absolute;left:128px;top:58px;text-align:left}
.footer-brand .name{font-family:"Montserrat",Arial,sans-serif;font-weight:800;font-size:26px;color:var(--orange)}
.contact-line{display:flex;align-items:center;gap:14px;font-size:15px;margin-bottom:18px}
.contact-line .ic{width:30px;height:30px;border:1px solid var(--white);border-radius:50%;display:flex;align-items:center;justify-content:center}
.social{display:flex;gap:10px}
.social span{width:32px;height:32px;border:1px solid var(--white);border-radius:50%}
.market{font-family:"Montserrat",Arial,sans-serif;font-weight:700;font-size:34px;margin-top:24px}
.copy{font-size:12px;margin-top:16px;color:#ccc}
</style>
</head>
<body>

<header class="site-header">
  <nav class="nav-left"><span>HOME</span><span>ABOUT US</span><span>PRODUCTS</span></nav>
  <nav class="nav-right"><span>BLOG</span><span>CONTACT US</span>
    <svg width="18" height="18" viewBox="0 0 18 18"><circle cx="7.5" cy="7.5" r="5.5" fill="none" stroke="#222" stroke-width="2.2"/><line x1="11.5" y1="11.5" x2="16.5" y2="16.5" stroke="#222" stroke-width="2.5"/></svg>
    <svg width="22" height="20" viewBox="0 0 22 20"><path d="M1 2h4l3 11h11l2-8H6" fill="none" stroke="#222" stroke-width="2"/><circle cx="9" cy="17" r="1.8" fill="#222"/><circle cx="18" cy="17" r="1.8" fill="#222"/></svg>
  </nav>
</header>
<div class="brand-badge"><span class="dot"></span><span class="name">QUIBREL</span><span class="sub">OUTDOOR</span></div>

<section class="hero">
  <div class="hero-photo" role="img" aria-label="Angler tying a fly at a lake at sunset"></div>
  <svg class="hero-curve" width="1200" height="140" viewBox="0 0 1200 140">
    <path d="M0 20 Q600 150 1200 20 L1200 140 L0 140Z" fill="#fff"/>
    <path d="M0 20 Q600 150 1200 20" fill="none" stroke="#f08a24" stroke-width="8"/>
  </svg>
  <div class="hero-copy">
    <h1>QUIBREL OUTDOOR</h1>
    <p>Lorem ipsum dolor sit amet, consectetur adipiscing elit sed do eiusmod tempor incididunt labore.</p>
    <span class="btn">Get Started ›</span>
  </div>
  <span class="slide-arrow" style="left:30px"><svg width="12" height="14" viewBox="0 0 12 14"><path d="M9 1L3 7l6 6" fill="none" stroke="#222" stroke-width="2.5"/></svg></span>
  <span class="slide-arrow" style="right:30px"><svg width="12" height="14" viewBox="0 0 12 14"><path d="M3 1l6 6-6 6" fill="none" stroke="#222" stroke-width="2.5"/></svg></span>
</section>

<section class="products" style="top:820px">
  <h2 class="heading">OUR PRODUCTS</h2>
  <div class="product-row">
    <div class="product-card"><div class="thumb" role="img" aria-label="Fly fishing glasses" style="background:linear-gradient(#eee,#b9bcc4)"></div><h3>Glasses Fly Fishing</h3><div class="price">$15.00</div><span class="btn btn-outline">Buy On Tradovik</span></div>
    <div class="product-card"><div class="thumb" role="img" aria-label="Golf towel" style="background:linear-gradient(#eee,#9a8f86)"></div><h3>Golf Towel</h3><div class="price">$15.00</div><span class="btn">Buy On Tradovik</span></div>
    <div class="product-card"><div class="thumb" role="img" aria-label="Folding camping table" style="background:linear-gradient(#ddd,#222)"></div><h3>Camping Table</h3><div class="price">$15.00</div><span class="btn btn-outline">Buy On Tradovik</span></div>
    <div class="product-card"><div class="thumb" role="img" aria-label="Fishing accessory" style="background:linear-gradient(#eee,#e09a4a)"></div><h3>Fishing</h3><div class="price">$15.00</div><span class="btn btn-outline">Buy On Tradovik</span></div>
  </div>
</section>

<section class="about">
  <div class="about-photo" role="img" aria-label="Smiling fisherman in hat and vest holding a rod"></div>
  <div class="about-card">
    <h2>ABOUT US</h2>
    <p>Lorem ipsum dolor sit amet, consectetur adipiscing elit, do eiusmod tempor incididunt ut labore et dolore magna aliqua. Ut enim ad minim veniam, quis nostrud exercitation ullamco laboris nisi ut aliquip commodo consequat; perspiciatis unde omnis iste natus error sit voluptatem accusantium doloremque laudantium.</p>
    <span class="btn">Learn More ›</span>
  </div>
</section>

<section class="products" style="top:1812px">
  <h2 class="heading">FEATURES PRODUCTS</h2>
  <div class="product-row">
    <div class="product-card"><div class="thumb" role="img" aria-label="Motor boat" style="background:linear-gradient(#f4f4f4,#5a6270)"></div><h3>Boat</h3><div class="price">$15.00</div><span class="btn btn-outline">Buy On Tradovik</span></div>
    <div class="product-card"><div class="thumb" role="img" aria-label="Golf club" style="background:linear-gradient(#f4f4f4,#a0a3a8)"></div><h3>Golf</h3><div class="price">$15.00</div><span class="btn">Buy On Tradovik</span></div>
    <div class="product-card"><div class="thumb" role="img" aria-label="Water tank container" style="background:linear-gradient(#e8f0fb,#3a7fd0)"></div><h3>Tank Widget</h3><div class="price">$15.00</div><span class="btn btn-outline">Buy On Tradovik</span></div>
    <div class="product-card"><div class="thumb" role="img" aria-label="Storage bag" style="background:linear-gradient(#eee,#555)"></div><h3>Storage Bag</h3><div class="price">$15.00</div><span class="btn btn-outline">Buy On Tradovik</span></div>
  </div>
</section>

<section class="newsletter">
  <h2>NEWSLETTER</h2>
  <p>Lorem ipsum dolor sit amet, consectetur adipiscing elit, sed do eiusmod tempor incididunt ut labore et dolore magna aliqua. Ut enim ad minim veniam, quis nostrud exercitation ullamco.</p>
  <div class="signup"><div class="field">Email Address</div><div class="submit">Subscribe</div></div>
</section>

<section class="blog">
  <h2 class="heading">OUR BLOG</h2>
  <div class="blog-row">
    <article class="post"><div class="photo" role="img" aria-label="Angler holding a catch" style="background:linear-gradient(135deg,#8fa07a,#c98a5a)"></div><div class="body"><span class="date">18.12.2021</span><h3>LOREM IPSUM CONSECTETUR</h3><p>Lorem ipsum dolor, consectetur adipiscing elit sed do eiusmod tempor.</p><div class="more">Learn More →</div></div></article>
    <article class="post"><div class="photo" role="img" aria-label="Fishing gear on a boat deck" style="background:linear-gradient(135deg,#7c9468,#3d4a3a)"></div><div class="body"><span class="date">18.12.2021</span><h3>LOREM IPSUM CONSECTETUR</h3><p>Lorem ipsum dolor, consectetur adipiscing elit sed do eiusmod tempor.</p><div class="more">Learn More →</div></div></article>
    <article class="post"><div class="photo" role="img" aria-label="Camping chairs under a canopy" style="background:linear-gradient(135deg,#b8c0c8,#5c6470)"></div><div class="body"><span class="date">18.12.2021</span><h3>LOREM IPSUM CONSECTETUR</h3><p>Lorem ipsum dolor, consectetur adipiscing elit sed do eiusmod tempor.</p><div class="more">Learn More →</div></div></article>
  </div>
</section>

<footer class="site-footer">
  <svg class="footer-curve" width="1200" height="120" viewBox="0 0 1200 120">
    <path d="M0 0 H1200 V60 Q600 -40 0 60Z" fill="#fff"/>
    <path d="M0 60 Q600 -40 1200 60" fill="none" stroke="#f08a24" stroke-width="6"/>
  </svg>
  <div class="footer-brand"><div class="name">QUIBREL</div><div style="color:var(--orange);font-size:12px;letter-spacing:3px;font-weight:600">OUTDOOR</div></div>
  <div class="footer-col" style="left:128px">
    <h4>CONTACT US</h4>
    <div class="contact-line"><span class="ic"><svg width="14" height="14" viewBox="0 0 14 14"><path d="M3 1l3 3-2 2a8 8 0 004 4l2-2 3 3-2 2C6 13 1 8 1 3z" fill="#fff"/></svg></span>555-0142-870</div>
    <div class="contact-line"><span class="ic"><svg width="14" height="12" viewBox="0 0 14 12"><rect x="1" y="1" width="12" height="10" fill="none" stroke="#fff" stroke-width="1.5"/><path d="M1 1l6 5 6-5" fill="none" stroke="#fff" stroke-width="1.5"/></svg></span>info@quibreloutdoor.com</div>
  </div>
  <div class="footer-col" style="left:448px"><h4>QUICKLINKS</h4><ul><li>Home</li><li>About us</li><li>products</li><li>Blog</li><li>Contact Us</li></ul></div>
  <div class="footer-col" style="left:672px"><h4>USEFUL LINKS</h4><ul><li>Contact Us</li><li>FAQ</li><li>Services</li><li>Privacy</li><li>Policy</li></ul></div>
  <div class="footer-col" style="left:880px">
    <h4>FOLLOW ON</h4>
    <div class="social"><span></span><span></span><span></span><span></span></div>
    <div class="market">Tradovik</div>
    <div class="copy">© 2021 Copyrights Quibrel Outdoor.</div>
  </div>
</footer>

</body>
</html>
```